KRT Flyer to attract applicants 11x17

Lantern Stagehand Collective provides crew for local concerts, filming, theater, and corporate events.
The flyer will be posted on bulletin boards at colleges with theater programs.
Our primary venues are historic theaters in downtown LA
Need a 11x17 poster to attract potential applicants/crew
I have attached a poster that one of our staff made that has all if the relevant info - but i know the poster can look much better than that. I have also attached many images and our logo. It is not necessary to use all of the images, or any of them. The two images of the theater interiors are the venues we operate so they would be the first to include. I can send additional info or images upon request. Thank you

Industry/Entity Type

Entertainment

Requirements
Must have
• APPLY@KRTCREW.EXAMPLE

```html
<!DOCTYPE html>
<html lang="en">
<head>
<meta charset="utf-8">
<title>Lantern Stagehand Collective – Open Positions</title>
<link rel="stylesheet" href="https://fonts.googleapis.com/css2?family=Poppins:wght@400;500;700;800;900&display=swap">
<style>
  :root {
    --stage-bg: #ebebeb;
    --paper: #ffffff;
    --brand-blue: #1f64c8;
    --brand-blue-deep: #1a52a8;
    --night: #1c1b2e;
    --violet: #6a5ad8;
    --text-grey: #8a8f98;
    --white: #ffffff;
  }
  * { box-sizing: border-box; margin: 0; padding: 0; }
  html, body {
    width: 1200px; height: 1200px; overflow: hidden;
    background: var(--stage-bg);
    font-family: "Poppins", sans-serif;
  }
  .poster {
    position: absolute; left: 250px; top: 50px;
    width: 700px; height: 1100px;
    background: var(--paper);
    overflow: hidden;
    box-shadow: 0 6px 24px rgba(0,0,0,0.12);
  }
  .poster__art { position: absolute; left: 0; top: 0; }
  .content {
    position: absolute; left: 40px; right: 40px; top: 532px;
    display: flex; flex-direction: column; align-items: center;
    text-align: center;
  }
  .brand {
    display: flex; align-items: center; gap: 12px;
    margin-bottom: 20px;
  }
  .brand__mark {
    width: 30px; height: 30px; border-radius: 50%;
    background: var(--brand-blue);
  }
  .brand__name {
    font-weight: 700; font-size: 20px; color: var(--brand-blue);
    letter-spacing: 0.5px; text-transform: uppercase;
  }
  .headline {
    font-weight: 900; font-size: 76px; line-height: 0.95;
    color: var(--brand-blue); letter-spacing: 1px;
    text-transform: uppercase;
    margin-bottom: 28px;
  }
  .pitch {
    width: 530px; padding: 26px 44px;
    border-radius: 80px;
    background: var(--brand-blue);
    color: var(--white);
    font-weight: 500; font-size: 23px; line-height: 1.3;
    margin-bottom: 34px;
  }
  .apply {
    font-weight: 800; font-size: 24px; color: var(--brand-blue);
    white-space: nowrap;
  }
  .footer-band {
    position: absolute; left: 0; right: 0; bottom: 0; height: 92px;
    background: var(--brand-blue);
    display: flex; align-items: center; justify-content: center;
  }
  .footer-band__url {
    color: var(--white); font-weight: 500; font-size: 26px; letter-spacing: 3px;
  }
</style>
</head>
<body>
  <main class="poster">
    <svg class="poster__art" width="700" height="1100" viewBox="0 0 700 1100">
      <defs>
        <linearGradient id="concertGlow" x1="0" y1="0" x2="0.3" y2="1">
          <stop offset="0" stop-color="#15142a"/>
          <stop offset="0.45" stop-color="#4a4aa0"/>
          <stop offset="0.7" stop-color="#a9aee0"/>
          <stop offset="1" stop-color="#2a2850"/>
        </linearGradient>
        <radialGradient id="theaterWarm" cx="0.5" cy="0.45" r="0.6">
          <stop offset="0" stop-color="#e7a35a"/>
          <stop offset="0.6" stop-color="#8a4a3a"/>
          <stop offset="1" stop-color="#3a2440"/>
        </radialGradient>
        <radialGradient id="theaterGold" cx="0.5" cy="0.5" r="0.6">
          <stop offset="0" stop-color="#f0c27a"/>
          <stop offset="0.6" stop-color="#b8753a"/>
          <stop offset="1" stop-color="#5a3424"/>
        </radialGradient>
        <radialGradient id="rigViolet" cx="0.5" cy="0.5" r="0.6">
          <stop offset="0" stop-color="#b8b0f5"/>
          <stop offset="0.6" stop-color="#7a66e0"/>
          <stop offset="1" stop-color="#3a2e90"/>
        </radialGradient>
      </defs>

      <rect class="frame" x="40" y="250" width="620" height="730" fill="none" stroke="var(--brand-blue)" stroke-width="3"/>

      <path class="header-rim" d="M0 0 H700 V230 Q520 430 250 430 Q90 430 0 360 Z" fill="var(--brand-blue)"/>
      <path class="header-photo" role="img" aria-label="Singer silhouetted on a concert stage under spotlights"
            d="M0 0 H700 V210 Q520 410 250 410 Q90 410 0 340 Z" fill="url(#concertGlow)"/>

      <circle class="venue-photo" role="img" aria-label="Historic theater interior with ornate ceiling and stage"
              cx="120" cy="420" r="82" fill="url(#theaterWarm)" stroke="var(--paper)" stroke-width="4"/>
      <circle class="venue-photo" role="img" aria-label="Historic theater auditorium with gilded balconies"
              cx="320" cy="410" r="88" fill="url(#theaterGold)" stroke="var(--paper)" stroke-width="4"/>
      <circle class="venue-photo" role="img" aria-label="Stage rigging lit in violet light"
              cx="590" cy="140" r="86" fill="url(#rigViolet)" stroke="var(--paper)" stroke-width="4"/>
    </svg>

    <section class="content">
      <div class="brand">
        <span class="brand__mark"></span>
        <span class="brand__name">Lantern Stagehand Collective</span>
      </div>
      <h1 class="headline">Has Open<br>Positions</h1>
      <p class="pitch">We are looking for talented technicians to add to our roster of skilled professionals.</p>
      <p class="apply">Send resume to : APPLY@KRTCREW.EXAMPLE</p>
    </section>

    <footer class="footer-band">
      <span class="footer-band__url">www.krtcrew.example</span>
    </footer>
  </main>
</body>
</html>
```